FinTech company looking to revamp and expand client-facing interface for our financial models

Pellworth Engines currently has a very simple website that allows clients to interact with our financial models. We are looking to completely redesign the current site and add several extra pages to provide extra functionality. We want the design to have a modern, slick feel, that will work on both a desktop or a tablet. It should be straightforward for clients to move between different pages at any time, and clear from the layout how to interact with the more advanced features. We have included screenshots of existing pages in the attached design brief, as well as sketches of the functionality required by the new pages, but can't provide a direct link to the current site.
Target Market(s)
Professional investors that will be paying to access the interface
Industry/Entity Type
Finance
Number of Pages Required
4 page
Colors
Designer to choose colors to be used in the design.
Look and feel
Each slider illustrates characteristics of the customer's brand and the style your logo design should communicate.

```html
<!DOCTYPE html>
<html lang="en">
<head>
<meta charset="utf-8">
<title>Ledgerline – ETF Pairs</title>
<link href="https://fonts.googleapis.com/css2?family=Open+Sans:wght@600;700&family=Roboto+Condensed:wght@400&display=swap" rel="stylesheet">
<style>
:root{
  --navy:#00306a;
  --teal:#006b68;
  --ink:#1a1a1a;
  --grey-band:#9b9b9b;
  --page:#e6e6e6;
  --panel:#ececec;
  --white:#ffffff;
  --row-alt:#efefef;
  --olive:#b5b33a;
  --blue:#3a6fb0;
  --green:#4aa83a;
}
*{box-sizing:border-box;margin:0;padding:0}
html,body{width:1033px;height:1200px;overflow:hidden;background:var(--page)}
.stage{position:absolute;left:0;top:0;width:1300px;height:1510px;transform:scale(.7946);transform-origin:0 0;font-family:"Open Sans",sans-serif;background:var(--page)}
.app{position:absolute;left:15px;top:15px;width:1270px;height:1480px;background:var(--panel)}
.tabstrip-bg{position:absolute;left:0;top:60px;width:1270px;height:95px;background:#f2f2f2}
.abs{position:absolute}
.topnav{position:absolute;left:15px;top:15px;width:1270px;height:60px;background:var(--white);box-shadow:0 3px 8px rgba(0,0,0,.08)}
.brand{position:absolute;left:58px;top:0;line-height:60px;font-weight:700;font-size:19px;color:var(--ink)}
.period{position:absolute;top:0;width:90px;height:60px;line-height:60px;text-align:center;font-weight:700;font-size:14px;color:var(--ink);border-right:1px solid #e4e4e4}
.period.active{background:var(--navy);color:var(--white);border:none}
.navlink{position:absolute;top:0;height:60px;display:flex;align-items:center;justify-content:center;gap:8px;font-weight:700;font-size:13px;color:var(--ink);border-left:1px solid #e4e4e4}
.tab{position:absolute;width:155px;background:var(--white);font-weight:600;font-size:13px;color:#333;text-align:center;box-shadow:0 1px 4px rgba(0,0,0,.08)}
.tab.active{background:var(--ink);color:var(--white);font-weight:700}
.bar{position:absolute;left:70px;width:1160px;height:50px;color:var(--white);font-weight:600;font-size:17px;line-height:50px;padding-left:28px}
.bar.selected{background:var(--navy)}
.bar.unselected{background:var(--grey-band)}
.bar svg{position:absolute;right:26px;top:11px}
.grid{position:absolute;left:70px;width:1160px;border-collapse:collapse;box-shadow:0 2px 6px rgba(0,0,0,.08)}
.grid th{height:70px;color:var(--white);font-weight:600;font-size:17px;background:var(--teal);border-left:1px solid #0a5b58}
.grid th:first-child{background:var(--ink);width:440px;border:none}
.grid td{height:70px;text-align:center;font-family:"Roboto Condensed",sans-serif;font-size:18px;color:var(--ink);background:var(--white);border-left:1px solid #ededed}
.grid tr:nth-child(even) td{background:var(--row-alt)}
.chart-card{position:absolute;left:70px;top:990px;width:1160px;height:425px;background:var(--white);box-shadow:0 2px 6px rgba(0,0,0,.08)}
.chart-head{position:absolute;left:0;top:0;width:1160px;height:85px;background:#efefef}
.ctab{position:absolute;background:var(--white);font-weight:700;font-size:13px;color:#444;text-align:center}
.ctab.chart{background:var(--navy);color:var(--white)}
.ctab.active{background:var(--ink);color:var(--white)}
.plot{position:absolute;left:70px;top:1075px}
.axis{font-family:"Open Sans",sans-serif;font-size:11px;fill:#555;font-weight:600}
</style>
</head>
<body>
<div class="stage">
  <div class="app"><div class="tabstrip-bg"></div></div>

  <header class="topnav">
    <div class="brand">Ledgerline</div>
    <div class="period active" style="left:180px">250D</div>
    <div class="period" style="left:270px">83D</div>
    <div class="period" style="left:360px">42D</div>
    <div class="navlink" style="left:755px;width:141px">
      <svg width="24" height="22" viewBox="0 0 24 22"><path d="M2 11 12 2l10 9M5 9v11h5v-6h4v6h5V9" fill="none" stroke="#1a1a1a" stroke-width="2.4"/></svg>MODELS</div>
    <div class="navlink" style="left:896px;width:177px">
      <svg width="24" height="24" viewBox="0 0 24 24"><circle cx="12" cy="12" r="4" fill="none" stroke="#1a1a1a" stroke-width="2"/><circle cx="12" cy="12" r="9" fill="none" stroke="#1a1a1a" stroke-width="2" stroke-dasharray="2 2.4"/></svg>SENSITIVITIES</div>
    <div class="navlink" style="left:1073px;width:197px">
      <svg width="24" height="24" viewBox="0 0 24 24"><path d="M12 2l3 7 7 .6-5.4 4.6 1.7 7.2L12 17.6 5.7 21.4l1.7-7.2L2 9.6 9 9z" fill="none" stroke="#1a1a1a" stroke-width="1.8"/></svg>FAVOURITES</div>
  </header>

  <nav>
    <div class="tab" style="left:70px;top:135px;height:35px;line-height:35px">EQUITIES</div>
    <div class="tab" style="left:230px;top:135px;height:35px;line-height:35px">ETFS</div>
    <div class="tab" style="left:390px;top:125px;height:45px;line-height:45px">PAIRS</div>
    <div class="tab active" style="left:550px;top:115px;height:55px;line-height:55px">ETF PAIRS</div>
    <div class="tab" style="left:710px;top:125px;height:45px;line-height:45px">FACTORS</div>
    <div class="tab" style="left:870px;top:135px;height:35px;line-height:35px">NEW TAB TITLE #1</div>
    <div class="tab" style="left:1030px;top:135px;height:35px;line-height:35px">NEW TAB TITLE #2</div>
    <div class="tab" style="left:1190px;top:135px;width:40px;height:35px;padding-top:8px"><svg width="14" height="20" viewBox="0 0 14 20"><path d="M3 2l8 8-8 8" fill="none" stroke="#666" stroke-width="3"/></svg></div>
    <div class="tab" style="left:1235px;top:135px;width:40px;height:35px;background:var(--navy);padding-top:5px"><svg width="26" height="26" viewBox="0 0 26 26"><circle cx="13" cy="13" r="11" fill="none" stroke="#fff" stroke-width="2"/><path d="M13 7v12M7 13h12" stroke="#fff" stroke-width="2"/></svg></div>
  </nav>

  <div class="bar selected" style="top:210px">Number of Selected Factors : 3
    <svg width="28" height="28" viewBox="0 0 28 28"><circle cx="14" cy="14" r="12.5" fill="none" stroke="#fff" stroke-width="2"/><path d="M8 17l6-6 6 6" fill="none" stroke="#fff" stroke-width="2.5"/></svg></div>
  <table class="grid" style="top:270px">
    <tr><th>ID &#8964;</th><th>Stat 1</th><th>Stat 2</th><th>Stat 3</th><th>Stat 4</th></tr>
    <tr><td>Factor 1</td><td>-1.4</td><td>0.094</td><td>6.1</td><td>100</td></tr>
    <tr><td>Factor 2</td><td>2.8</td><td>0.085</td><td>3.1</td><td>0.7</td></tr>
    <tr><td>Factor 3</td><td>-3.7</td><td>2.7</td><td>-7.2</td><td>100</td></tr>
  </table>

  <div class="bar unselected" style="top:600px">Unselected Factors
    <svg width="28" height="28" viewBox="0 0 28 28"><circle cx="14" cy="14" r="12.5" fill="none" stroke="#fff" stroke-width="2"/><path d="M8 17l6-6 6 6" fill="none" stroke="#fff" stroke-width="2.5"/></svg></div>
  <table class="grid" style="top:660px">
    <tr><th>Factor</th><th>Factor</th><th>Factor</th><th>Factor</th><th>Factor</th></tr>
    <tr><td>Factor</td><td>Factor</td><td>Factor</td><td>Factor</td><td>Factor</td></tr>
    <tr><td>Factor</td><td>Factor</td><td>Factor</td><td>Factor</td><td>Factor</td></tr>
    <tr><td>Factor</td><td>Factor</td><td>Factor</td><td>Factor</td><td>Factor</td></tr>
  </table>

  <section class="chart-card">
    <div class="chart-head"></div>
    <div class="ctab chart" style="left:55px;top:50px;width:155px;height:35px;line-height:35px">CHART</div>
    <div class="ctab" style="left:215px;top:50px;width:90px;height:35px;line-height:35px">#1</div>
    <div class="ctab" style="left:310px;top:50px;width:90px;height:35px;line-height:35px">#2</div>
    <div class="ctab" style="left:405px;top:45px;width:90px;height:40px;line-height:40px">#3</div>
    <div class="ctab active" style="left:500px;top:40px;width:90px;height:45px;line-height:45px">#4</div>
  </section>

  <svg class="plot" width="1160" height="340" viewBox="70 1075 1160 340">
    <g stroke="#eee" stroke-width="1">
      <line x1="182" y1="1120" x2="182" y2="1325"/><line x1="324" y1="1120" x2="324" y2="1325"/>
      <line x1="465" y1="1120" x2="465" y2="1325"/><line x1="605" y1="1120" x2="605" y2="1325"/>
      <line x1="742" y1="1120" x2="742" y2="1325"/><line x1="882" y1="1120" x2="882" y2="1325"/>
      <line x1="1022" y1="1120" x2="1022" y2="1325"/>
      <line x1="155" y1="1138" x2="1077" y2="1138"/><line x1="155" y1="1175" x2="1077" y2="1175"/>
      <line x1="155" y1="1213" x2="1077" y2="1213"/><line x1="155" y1="1250" x2="1077" y2="1250"/>
      <line x1="155" y1="1288" x2="1077" y2="1288"/>
    </g>
    <line x1="155" y1="1325" x2="1077" y2="1325" stroke="#999"/>
    <g class="axis" text-anchor="end">
      <text x="150" y="1142">100</text><text x="150" y="1179">80</text><text x="150" y="1217">60</text>
      <text x="150" y="1254">40</text><text x="150" y="1292">20</text><text x="150" y="1329">0</text>
    </g>
    <g class="axis" text-anchor="middle">
      <text x="182" y="1350">Jul 2018</text><text x="324" y="1350">Sep 2018</text><text x="465" y="1350">Nov 2018</text>
      <text x="605" y="1350">Jan 2019</text><text x="742" y="1350">Mar 2019</text><text x="882" y="1350">May 2019</text>
      <text x="1022" y="1350">Jul 2019</text>
    </g>
    <g stroke-linecap="round" stroke-width="8" fill="none">
      <line x1="202" y1="1138" x2="290" y2="1138" stroke="var(--olive)" stroke-dasharray="0 6"/>
      <line x1="540" y1="1140" x2="580" y2="1140" stroke="var(--olive)" stroke-dasharray="0 7"/>
      <line x1="810" y1="1140" x2="1000" y2="1140" stroke="var(--olive)" stroke-dasharray="0 6"/>
      <line x1="590" y1="1138" x2="1028" y2="1138" stroke="var(--blue)" stroke-dasharray="0 7"/>
    </g>
    <g fill="var(--olive)">
      <circle cx="296" cy="1145" r="4"/><circle cx="300" cy="1140" r="4"/><circle cx="308" cy="1143" r="4"/><circle cx="318" cy="1140" r="4"/><circle cx="326" cy="1146" r="4"/><circle cx="334" cy="1149" r="4"/>
      <circle cx="337" cy="1205" r="4"/><circle cx="350" cy="1218" r="4"/><circle cx="342" cy="1235" r="4"/><circle cx="355" cy="1240" r="4"/><circle cx="348" cy="1252" r="4"/><circle cx="362" cy="1255" r="4"/><circle cx="370" cy="1232" r="4"/><circle cx="378" cy="1242" r="4"/><circle cx="382" cy="1198" r="4"/><circle cx="388" cy="1178" r="4"/><circle cx="395" cy="1166" r="4"/><circle cx="400" cy="1140" r="4"/><circle cx="409" cy="1143" r="4"/><circle cx="414" cy="1200" r="4"/><circle cx="418" cy="1215" r="4"/><circle cx="425" cy="1228" r="4"/><circle cx="430" cy="1222" r="4"/>
      <circle cx="435" cy="1300" r="4"/><circle cx="445" cy="1292" r="4"/><circle cx="450" cy="1276" r="4"/><circle cx="458" cy="1282" r="4"/><circle cx="462" cy="1268" r="4"/><circle cx="470" cy="1318" r="4"/><circle cx="478" cy="1310" r="4"/><circle cx="485" cy="1305" r="4"/><circle cx="494" cy="1290" r="4"/><circle cx="498" cy="1272" r="4"/><circle cx="508" cy="1262" r="4"/><circle cx="516" cy="1268" r="4"/><circle cx="522" cy="1250" r="4"/><circle cx="528" cy="1222" r="4"/><circle cx="534" cy="1210" r="4"/><circle cx="540" cy="1215" r="4"/>
      <circle cx="577" cy="1312" r="4"/><circle cx="582" cy="1316" r="4"/><circle cx="592" cy="1310" r="4"/><circle cx="600" cy="1306" r="4"/><circle cx="608" cy="1300" r="4"/><circle cx="616" cy="1303" r="4"/><circle cx="624" cy="1300" r="4"/><circle cx="632" cy="1306" r="4"/><circle cx="638" cy="1312" r="4"/><circle cx="645" cy="1295" r="4"/><circle cx="650" cy="1275" r="4"/><circle cx="656" cy="1273" r="4"/><circle cx="660" cy="1254" r="4"/><circle cx="658" cy="1238" r="4"/><circle cx="655" cy="1201" r="4"/><circle cx="668" cy="1201" r="4"/><circle cx="672" cy="1162" r="4"/><circle cx="686" cy="1158" r="4"/><circle cx="690" cy="1214" r="4"/><circle cx="694" cy="1282" r="4"/><circle cx="700" cy="1285" r="4"/><circle cx="703" cy="1296" r="4"/><circle cx="708" cy="1165" r="4"/><circle cx="712" cy="1193" r="4"/><circle cx="718" cy="1182" r="4"/><circle cx="720" cy="1240" r="4"/><circle cx="726" cy="1150" r="4"/><circle cx="734" cy="1160" r="4"/><circle cx="740" cy="1152" r="4"/><circle cx="752" cy="1152" r="4"/>
    </g>
    <g fill="var(--blue)">
      <circle cx="205" cy="1149" r="4"/><circle cx="212" cy="1142" r="4"/><circle cx="220" cy="1149" r="4"/><circle cx="203" cy="1203" r="4"/>
      <circle cx="223" cy="1219" r="4"/><circle cx="228" cy="1252" r="4"/><circle cx="234" cy="1245" r="4"/><circle cx="236" cy="1266" r="4"/><circle cx="240" cy="1272" r="4"/><circle cx="238" cy="1281" r="4"/><circle cx="250" cy="1255" r="4"/><circle cx="256" cy="1214" r="4"/><circle cx="258" cy="1240" r="4"/><circle cx="264" cy="1242" r="4"/><circle cx="270" cy="1218" r="4"/><circle cx="268" cy="1240" r="4"/><circle cx="275" cy="1280" r="4"/><circle cx="282" cy="1272" r="4"/><circle cx="288" cy="1255" r="4"/><circle cx="295" cy="1250" r="4"/><circle cx="300" cy="1278" r="4"/><circle cx="305" cy="1270" r="4"/><circle cx="312" cy="1280" r="4"/><circle cx="318" cy="1274" r="4"/><circle cx="322" cy="1278" r="4"/><circle cx="333" cy="1285" r="4"/><circle cx="338" cy="1305" r="4"/><circle cx="345" cy="1300" r="4"/><circle cx="352" cy="1298" r="4"/><circle cx="360" cy="1305" r="4"/><circle cx="366" cy="1298" r="4"/><circle cx="373" cy="1300" r="4"/><circle cx="380" cy="1282" r="4"/><circle cx="386" cy="1274" r="4"/><circle cx="394" cy="1268" r="4"/><circle cx="400" cy="1278" r="4"/><circle cx="406" cy="1285" r="4"/><circle cx="412" cy="1292" r="4"/><circle cx="418" cy="1270" r="4"/><circle cx="426" cy="1282" r="4"/><circle cx="432" cy="1322" r="4"/><circle cx="440" cy="1318" r="4"/><circle cx="446" cy="1295" r="4"/><circle cx="452" cy="1305" r="4"/><circle cx="460" cy="1270" r="4"/><circle cx="463" cy="1195" r="4"/><circle cx="468" cy="1168" r="4"/><circle cx="476" cy="1163" r="4"/><circle cx="480" cy="1152" r="4"/><circle cx="484" cy="1176" r="4"/><circle cx="490" cy="1173" r="4"/><circle cx="496" cy="1302" r="4"/><circle cx="502" cy="1290" r="4"/><circle cx="510" cy="1278" r="4"/><circle cx="518" cy="1262" r="4"/><circle cx="525" cy="1290" r="4"/><circle cx="530" cy="1258" r="4"/><circle cx="535" cy="1243" r="4"/><circle cx="540" cy="1245" r="4"/><circle cx="542" cy="1160" r="4"/><circle cx="548" cy="1148" r="4"/><circle cx="556" cy="1142" r="4"/><circle cx="564" cy="1148" r="4"/><circle cx="572" cy="1155" r="4"/>
    </g>
    <g fill="var(--green)"><circle cx="1000" cy="1322" r="4"/><circle cx="1006" cy="1322" r="4"/><circle cx="1010" cy="1322" r="4"/></g>
    <text x="1132" y="1140" font-family="Georgia,serif" font-size="12" fill="#444">Names</text>
    <g>
      <circle cx="1114" cy="1137" r="3.5" fill="#8fb0d8"/><circle cx="1114" cy="1155" r="3.5" fill="#f0a860"/>
      <circle cx="1114" cy="1174" r="3.5" fill="#3a9a3a"/><circle cx="1114" cy="1193" r="3.5" fill="#e07a7a"/>
      <circle cx="1114" cy="1211" r="3.5" fill="#b8a0d8"/><circle cx="1114" cy="1230" r="3.5" fill="#a89a90"/>
      <circle cx="1114" cy="1248" r="3.5" fill="#e8b8d8"/><circle cx="1114" cy="1267" r="3.5" fill="#b8b8b8"/>
      <circle cx="1114" cy="1286" r="3.5" fill="#b5b33a"/><circle cx="1114" cy="1304" r="3.5" fill="#8ed8e0"/>
      <circle cx="1114" cy="1323" r="3.5" fill="#3a6fb0"/>
    </g>
  </svg>
</div>
</body>
</html>
```